Banner for construction site to identify developer

we need a 4 foot by 8 foot banner to hang on the fence of a residential townhome development in Phoenix, Arizona that identifies Tolvane Holdings as the company behind the development/project. Also needs to include the logo, phone number, and web address. Would like to stick with the blue colors provided in the attached logo. The blues should stay the same but the letters in the logo can change to another color if necessary. Feel free to use "Tolvane Holdings" in place of "Tolvane Holdings Group". Looking for use of colors/design to take up space so banner is not just text with a logo.

Target Market(s)

drive by traffic looking at the site

Industry/Entity Type

Real Estate

Colors
0054AA
0677BA
7BADD7
CADEEF
E8F1F8

Requirements
Must have
• company name, phone number and web address

```html
<!DOCTYPE html>
<html lang="en">
<head>
<meta charset="utf-8">
<title>Tolvane Holdings – Site Banner</title>
<link rel="stylesheet" href="https://fonts.googleapis.com/css2?family=Montserrat:wght@700&display=swap">
<style>
  :root {
    --backdrop: #4a4a4a;
    --banner-white: #ffffff;
    --band-blue: #21709f;
    --accent-blue: #1fa8d9;
    --name-ink: #3a3a3c;
    --band-text: #ffffff;
  }
  * { margin: 0; padding: 0; box-sizing: border-box; }
  html, body {
    width: 885px;
    height: 1200px;
    overflow: hidden;
    background: var(--backdrop);
  }
  .canvas {
    width: 885px;
    height: 1200px;
    display: flex;
    align-items: center;
    justify-content: center;
  }
  .banner {
    width: 805px;
    height: 402px;
    background: var(--banner-white);
    display: flex;
    flex-direction: column;
    box-shadow: 0 6px 28px rgba(0,0,0,0.35);
  }
  .banner__identity {
    height: 236px;
    display: flex;
    align-items: center;
    justify-content: center;
    gap: 22px;
  }
  .identity__square {
    width: 62px;
    height: 62px;
    background: var(--accent-blue);
    flex: none;
  }
  .identity__name {
    font-family: "Montserrat", sans-serif;
    font-weight: 700;
    font-size: 50px;
    line-height: 1.05;
    letter-spacing: -1px;
    color: var(--name-ink);
  }
  .identity__name span { display: block; }
  .identity__name .name__suffix { text-align: right; }
  .banner__contact {
    flex: 1;
    background: var(--band-blue);
    color: var(--band-text);
    font-family: "Montserrat", sans-serif;
    font-weight: 700;
    display: flex;
    flex-direction: column;
    align-items: center;
    justify-content: center;
    gap: 6px;
  }
  .contact__phone {
    display: flex;
    align-items: center;
    gap: 12px;
    font-size: 58px;
    line-height: 1;
    letter-spacing: 1px;
  }
  .contact__phone-icon { width: 42px; height: 42px; flex: none; }
  .contact__web {
    font-size: 38px;
    line-height: 1.1;
    letter-spacing: 0.5px;
  }
</style>
</head>
<body>
  <main class="canvas">
    <section class="banner">
      <header class="banner__identity">
        <div class="identity__square" aria-hidden="true"></div>
        <h1 class="identity__name">
          <span>Tolvane Holdings</span>
          <span class="name__suffix">Group</span>
        </h1>
      </header>
      <footer class="banner__contact">
        <p class="contact__phone">
          <svg class="contact__phone-icon" viewBox="0 0 48 48" aria-hidden="true">
            <path fill="#ffffff" d="M12 6c2-1 4-.5 5 1.5l4 7c1 2 .5 4-1.2 5.2l-2.6 1.8c1.8 4 5 7.5 9 9.6l1.9-2.5c1.2-1.7 3.4-2.2 5.2-1.1l6.7 4.3c1.8 1.2 2.3 3.4 1.3 5.2l-1.8 3c-1.6 2.6-4.7 3.8-7.6 2.8C20.6 38.5 9.5 27.4 6.2 15.8c-.8-3 .4-6.1 3-7.6z"/>
            <path fill="none" stroke="#ffffff" stroke-width="3" stroke-linecap="round" d="M28 12a9 9 0 0 1 8 8M28 5a16 16 0 0 1 15 15"/>
          </svg>
          (480) 555-0147
        </p>
        <p class="contact__web">www.tolvaneholdings.com</p>
      </footer>
    </section>
  </main>
</body>
</html>
```